Coastal Learner Bureau business cards

Australian company about to start offering its services. We recruit international students to come to study English, vocational education and postgraduate courses in Australia. We help them find the institution and select the right city they want to come to Australia. We are a young, online oriented and supportive agency. Our clients are between 18 and 35 years old, mainly University students, young professionals or people with work experience. We provide much more information that any other agency offer. We administrate a Facebook group with more than 11.000 members that daily ask questions about general information when coming to Australia, while they are here and even after they leave the country

Target Market(s)

International students from South America, Central America and Europe

Industry/Entity Type

Student

Contact Information for Business Card

Tomas Bilbrea
Managing Director
tomas@kelvarin.com.au
www.kelvoria.com.au
+61 491058264
Melbourne, Australia

Font styles to use
Serif
Sans Serif

Colors

Designer to choose colors to be used in the design.

Requirements
Must have
• Horizontal design
• Standard business card size and shape. If font uses green or yellow colours, they will have to match the ones from the logo
Nice to have
• UPDATE: Use the contents of the green image to design one of the card sides. Use our logo in the background of that side as watermark.
• Passport image, or immigration stamps. A picture of the Yarra River (from Melbourne) would be cool as well.
Should not have
• Non-standard business card size and shape
• Not black as the background colour of any sides as we are not a VIP agency or a hight class service. We are orientes to young people and they like colours, pictures, something attractive.
• Vertical design
• NO YELLOW or BLACK AS THE BACKGROUND COLOUR OF ANY SIDE OF THE BIZ CARD

```html
<!DOCTYPE html>
<html lang="en">
<head>
<meta charset="utf-8">
<title>Coastal Learner Bureau business cards</title>
<link rel="stylesheet" href="https://fonts.googleapis.com/css2?family=Arimo:wght@400;700&display=swap">
<style>
  :root {
    --page: #e6e6e3;
    --green: #1b5e3b;
    --green-dark: #164f31;
    --gold: #d9b21c;
    --ink: #1e1e1e;
    --white: #ffffff;
    --tan-light: #e0cf9c;
    --tan: #c8b27a;
    --stamp-teal: #4f9a95;
    --stamp-grey: #b9b4a6;
  }
  * { box-sizing: border-box; margin: 0; padding: 0; }
  html, body {
    width: 1200px; height: 997px; overflow: hidden;
    background: var(--page);
    font-family: "Arimo", Arial, sans-serif;
  }
  .canvas { position: relative; width: 1200px; height: 997px; }
  .card {
    position: absolute; left: 250px; width: 700px; height: 400px;
    border-radius: 24px; overflow: hidden;
    box-shadow: 0 6px 18px rgba(0,0,0,.18);
  }

  /* Back side */
  .card-back {
    top: 66px;
    background: radial-gradient(ellipse at 60% 40%, var(--tan-light), var(--tan));
  }
  .card-back .stamps {
    position: absolute; left: 0; top: 0; width: 330px; height: 400px;
    background: linear-gradient(200deg, rgba(185,180,166,0) 0%, var(--stamp-grey) 35%, rgba(201,178,122,.6) 60%, var(--stamp-teal) 100%);
    opacity: .85;
  }
  .card-back .brand {
    position: absolute; left: 380px; top: 120px;
    display: flex; align-items: center; gap: 14px;
    color: var(--white); font-size: 62px; font-weight: 700;
  }
  .card-back .brand-dot { width: 22px; height: 22px; border-radius: 50%; background: var(--white); }
  .card-back .web {
    position: absolute; right: 36px; bottom: 40px;
    color: var(--green); font-weight: 700; font-size: 19px;
  }

  /* Front side */
  .card-front { top: 531px; background: var(--white); }
  .card-front .bands { position: absolute; inset: 0; }
  .card-front .brand {
    position: absolute; left: 0; right: 0; top: 48px;
    display: flex; justify-content: center; align-items: center; gap: 12px;
    color: var(--green); font-size: 46px; font-weight: 700;
  }
  .card-front .brand-dot { width: 16px; height: 16px; border-radius: 50%; background: var(--gold); }
  .person { position: absolute; left: 36px; top: 176px; }
  .person-name { color: var(--green); font-weight: 700; font-size: 20px; letter-spacing: .5px; }
  .person-role { color: var(--ink); font-size: 16px; margin-top: 3px; }
  .company {
    position: absolute; right: 32px; top: 202px; text-align: right;
    color: var(--ink); font-size: 15px; line-height: 1.25;
  }
  .company-name { color: var(--green); font-weight: 700; font-size: 16px; letter-spacing: .5px; }
  .card-front .web {
    position: absolute; right: 34px; top: 306px;
    color: var(--gold); font-weight: 700; font-size: 19px;
  }
  .contacts { position: absolute; left: 36px; top: 270px; list-style: none; }
  .contacts li {
    display: flex; align-items: center; gap: 10px;
    color: var(--ink); font-size: 17px; height: 28px;
  }
  .contacts svg { width: 18px; height: 18px; flex: none; }
</style>
</head>
<body>
<main class="canvas">

  <section class="card card-back" aria-label="Business card, back side">
    <div class="stamps" role="img" aria-label="Passport immigration stamps: arrival, Australia and approved stamps"></div>
    <div class="brand"><span>Kelvoria</span><span class="brand-dot"></span></div>
    <p class="web">www.kelvoria.com.au</p>
  </section>

  <section class="card card-front" aria-label="Business card, front side">
    <svg class="bands" viewBox="0 0 700 400" width="700" height="400" aria-hidden="true">
      <line x1="226" y1="193" x2="672" y2="193" stroke="var(--green)" stroke-width="1.5"/>
      <rect x="0" y="340" width="458" height="8" rx="4" fill="var(--gold)"/>
      <path d="M700 288 H500 C480 288 478 350 450 354 H0 V372 H700 Z" fill="var(--green)"/>
    </svg>
    <div class="brand"><span>Kelvoria</span><span class="brand-dot"></span></div>
    <div class="person">
      <p class="person-name">TOMAS BILBREA</p>
      <p class="person-role">Managing Director</p>
    </div>
    <div class="company">
      <p class="company-name">KELVORIA PVT LTD.</p>
      <p>27 Harlow Lane, Box 412,</p>
      <p>Melbourne, Australia 3004</p>
    </div>
    <p class="web">www.kelvoria.com.au</p>
    <ul class="contacts">
      <li>
        <svg viewBox="0 0 18 18"><circle cx="9" cy="9" r="9" fill="var(--green)"/><path d="M5.5 6.5c0 3.5 2.5 6 6 6l1-1.5-2-1-1 .8c-1-.5-1.8-1.3-2.3-2.3l.8-1-1-2z" fill="var(--white)"/></svg>
        +61 491058264
      </li>
      <li>
        <svg viewBox="0 0 18 18"><circle cx="9" cy="9" r="9" fill="var(--green)"/><rect x="4.5" y="6" width="9" height="6.5" fill="none" stroke="var(--white)" stroke-width="1.2"/><path d="M4.5 6l4.5 3.8L13.5 6" fill="none" stroke="var(--white)" stroke-width="1.2"/></svg>
        tomas@kelvarin.com.au
      </li>
    </ul>
  </section>

</main>
</body>
</html>
```